Black Matte card with samurai logo which I would like it to be textured and company name on one side and on the other side I would like the company information with the reno (Face logo) Sushi logo. Double Sided card.

majority customers are University students, University sororities and fraternities.

It Company

Reno Sushi
317 W. Harlow Ave
Tucson, AZ 85042
Phone (520)413-6271
Fax (520)357-1846
E-mail: Renosushidesert@mailbox-example.com
FB: Renosushidesert
Twitter: Renosushidesert

• Present Normal

```html
<!DOCTYPE html>
<html lang="en">
<head>
<meta charset="utf-8">
<title>Reno Sushi — Business Card</title>
<link rel="stylesheet" href="https://fonts.googleapis.com/css2?family=PT+Sans:wght@400;700&display=swap">
<style>
  :root {
    --stage: #e9e6e1;
    --card-white: #ffffff;
    --ink: #3a3a3a;
    --red: #a3242a;
    --red-dark: #7a1419;
    --black: #1d1d1d;
    --divider: #d4d4d4;
    --texture-light: #3a3a3a;
    --texture-dark: #0e0e0e;
  }
  * { margin: 0; padding: 0; box-sizing: border-box; }
  html, body { width: 1200px; height: 986px; overflow: hidden; }
  body {
    background: var(--stage);
    font-family: "PT Sans", Arial, sans-serif;
    position: relative;
  }
  .card {
    position: absolute;
    width: 771px;
    height: 439px;
    border-radius: 26px;
    overflow: hidden;
    box-shadow: 0 2px 6px rgba(0,0,0,0.18);
  }
  .card-front { left: 50px; top: 44px; background: var(--card-white); }
  .card-back { left: 386px; top: 513px; background: var(--black); }

  .brand {
    position: absolute;
    left: 76px;
    top: 50px;
    width: 240px;
    text-align: center;
  }
  .brand-mark {
    width: 150px; height: 150px;
    border-radius: 50%;
    background: var(--black);
    margin: 0 auto;
  }
  .brand-name {
    color: var(--red);
    font-weight: 400;
    font-size: 58px;
    line-height: 1;
    margin-top: 16px;
    letter-spacing: 1px;
  }
  .brand-name .sub {
    display: block;
    font-size: 29px;
    letter-spacing: 3px;
    margin-top: 2px;
  }
  .divider {
    position: absolute;
    left: 340px; top: 102px;
    width: 1px; height: 168px;
    background: var(--divider);
  }
  .contact {
    position: absolute;
    left: 364px; top: 116px;
    list-style: none;
    color: var(--ink);
    font-size: 19px;
  }
  .contact li { display: flex; align-items: center; height: 30px; }
  .contact svg { width: 18px; height: 18px; margin-right: 10px; fill: var(--red); }
  .address {
    position: absolute;
    left: 392px; top: 214px;
    color: var(--ink);
    font-size: 19px;
    line-height: 28px;
    font-style: normal;
  }
  .waves { position: absolute; left: 0; bottom: 0; width: 771px; height: 439px; }
  .social {
    position: absolute;
    left: 528px; top: 360px;
    list-style: none;
    color: #ffffff;
    font-size: 19px;
  }
  .social li { display: flex; align-items: center; height: 32px; }
  .social .chip {
    width: 20px; height: 20px;
    background: var(--red);
    border-radius: 3px;
    margin-right: 10px;
  }

  .texture {
    position: absolute; inset: 0;
    background:
      repeating-linear-gradient(180deg, rgba(255,255,255,0.05) 0 2px, transparent 2px 9px),
      radial-gradient(ellipse at 50% 45%, var(--texture-light), var(--texture-dark) 75%);
  }
  .back-brand {
    position: absolute;
    left: 0; right: 0; top: 92px;
    text-align: center;
  }
  .back-brand .brand-mark { width: 170px; height: 170px; background: var(--red); }
  .back-brand .brand-name { color: #ffffff; font-size: 48px; margin-top: 18px; }
</style>
</head>
<body>
  <section class="card card-front" aria-label="Card front">
    <div class="brand">
      <div class="brand-mark"></div>
      <div class="brand-name">reno<span class="sub">sushi</span></div>
    </div>
    <div class="divider"></div>
    <ul class="contact">
      <li>
        <svg viewBox="0 0 24 24"><path d="M6.6 10.8a15 15 0 0 0 6.6 6.6l2.2-2.2a1 1 0 0 1 1-.25 11.4 11.4 0 0 0 3.6.57 1 1 0 0 1 1 1V20a1 1 0 0 1-1 1A17 17 0 0 1 3 4a1 1 0 0 1 1-1h3.5a1 1 0 0 1 1 1c0 1.25.2 2.45.57 3.57a1 1 0 0 1-.25 1z"/></svg>
        (520)413-6271
      </li>
      <li>
        <svg viewBox="0 0 24 24"><path d="M7 1h10a2 2 0 0 1 2 2v18a2 2 0 0 1-2 2H7a2 2 0 0 1-2-2V3a2 2 0 0 1 2-2zm0 3v13h10V4zm5 15a1.2 1.2 0 1 0 0 2.4 1.2 1.2 0 0 0 0-2.4z"/></svg>
        (520)357-1846
      </li>
      <li>
        <svg viewBox="0 0 24 24"><path d="M2 5h20v14H2zm2 2v.5l8 5 8-5V7zm0 2.8V17h16V9.8l-8 5z"/></svg>
        Renosushidesert@mailbox-example.com
      </li>
    </ul>
    <address class="address">317 W. Harlow Ave Tucson<br>AZ 85042</address>
    <svg class="waves" viewBox="0 0 771 439" aria-hidden="true">
      <path d="M0 392 C 200 360, 420 300, 771 344 L771 439 L0 439 Z" fill="var(--black)"/>
      <path d="M0 384 C 180 378, 330 372, 560 384 C 430 374, 240 378, 0 396 Z" fill="var(--red-dark)"/>
      <path d="M0 400 C 150 392, 300 392, 460 410 C 330 396, 170 402, 0 420 Z" fill="var(--card-white)"/>
      <path d="M0 412 C 150 400, 300 405, 440 439 L0 439 Z" fill="var(--red)"/>
      <path d="M0 368 C 220 346, 470 310, 771 350 C 470 322, 220 356, 0 378 Z" fill="var(--red)"/>
    </svg>
    <ul class="social">
      <li><span class="chip"></span>Renosushidesert</li>
      <li><span class="chip"></span>Renosushidesert</li>
    </ul>
  </section>

  <section class="card card-back" aria-label="Card back">
    <div class="texture" role="img" aria-label="Black brushed matte texture"></div>
    <div class="back-brand">
      <div class="brand-mark"></div>
      <div class="brand-name">reno sushi</div>
    </div>
  </section>
</body>
</html>
```